Veldmark Supplies Business Card

Professional business card that stand out to our potential customers. Front and back with clean modern design

Industry/Entity Type

Oil and gas

Contact Information for Business Card

Name, address, website , office phone and cell number

Requirements
Must have
• Editable files for each employee

```html
<!DOCTYPE html>
<html lang="en">
<head>
<meta charset="utf-8">
<title>Veldmark Supplies Business Card</title>
<link href="https://fonts.googleapis.com/css2?family=Poppins:wght@400;600;700&display=swap" rel="stylesheet">
<style>
  :root {
    --page: #1b1b1b;
    --card: #262626;
    --card-edge: #303030;
    --red: #ec1c24;
    --blue: #19b2d8;
    --text: #e8e8e8;
    --rule: #4a4a4a;
    --silver: #d8d8d8;
  }
  * { box-sizing: border-box; margin: 0; padding: 0; }
  html, body { width: 1200px; height: 875px; overflow: hidden; }
  body {
    background: var(--page);
    font-family: "Poppins", sans-serif;
    position: relative;
  }
  .card {
    position: absolute;
    width: 540px;
    height: 310px;
    border-radius: 18px;
    overflow: hidden;
    background: var(--card);
    box-shadow: 0 20px 40px rgba(0,0,0,.55);
  }
  /* back side */
  .card-back { left: 40px; top: 282px; }
  .back-pattern {
    position: absolute; inset: 0;
    background: linear-gradient(100deg, #cfcfcf 0%, #7a7a7a 28%, #3a3a3a 55%, #111 80%, #080808 100%);
  }
  .back-brand {
    position: absolute; left: 50%; top: 50%;
    transform: translate(-50%, -50%);
    display: flex; align-items: center; gap: 10px;
    padding: 10px 16px;
    background: rgba(20,20,20,.85);
    border-radius: 6px;
  }
  .brand-mark { width: 14px; height: 14px; background: var(--red); }
  .brand-name {
    font-weight: 700; font-size: 20px; letter-spacing: 1px;
    text-transform: uppercase; color: var(--red);
  }
  /* front side */
  .card-front { right: 40px; top: 282px; border: 1px solid var(--card-edge); }
  .front-brand {
    position: absolute; left: 34px; top: 120px;
    display: flex; align-items: center; gap: 10px;
  }
  .front-brand .brand-name { font-size: 19px; }
  .divider {
    position: absolute; left: 268px; top: 58px;
    width: 1px; height: 160px; background: var(--rule);
  }
  .contact { position: absolute; left: 290px; top: 52px; color: var(--text); }
  .person-name { font-weight: 700; font-size: 22px; color: var(--red); line-height: 1.1; }
  .person-title { font-size: 11px; margin-bottom: 6px; }
  .address { font-size: 11px; line-height: 1.45; margin-bottom: 6px; }
  .contact-list { list-style: none; font-size: 11px; line-height: 1.65; }
  .contact-list li { display: flex; align-items: center; gap: 7px; }
  .contact-list svg { width: 10px; height: 10px; fill: var(--red); flex: none; }
  .card-bands { position: absolute; left: 0; bottom: 0; width: 540px; height: 14px; }
</style>
</head>
<body>

<section class="card card-back" aria-label="Card back">
  <div class="back-pattern" role="img" aria-label="Repeating embossed brand pattern in silver fading to black"></div>
  <div class="back-brand">
    <span class="brand-mark"></span>
    <span class="brand-name">Veldmark Supplies</span>
  </div>
</section>

<section class="card card-front" aria-label="Card front">
  <div class="front-brand">
    <span class="brand-mark"></span>
    <span class="brand-name">Veldmark Supplies</span>
  </div>
  <div class="divider"></div>
  <div class="contact">
    <p class="person-name">Corin Hale</p>
    <p class="person-title">President</p>
    <p class="address">412 N.Larkfield Suite 5<br>Midland, Tx 79701</p>
    <ul class="contact-list">
      <li><svg viewBox="0 0 10 10"><path d="M2 0h2l1 2.5-1.3 1a6 6 0 0 0 2.8 2.8l1-1.3L10 6v2a2 2 0 0 1-2 2A8 8 0 0 1 0 2a2 2 0 0 1 2-2z"/></svg>(555)210-4187</li>
      <li><svg viewBox="0 0 10 10"><path d="M2.5 0h5a1 1 0 0 1 1 1v8a1 1 0 0 1-1 1h-5a1 1 0 0 1-1-1V1a1 1 0 0 1 1-1zm.5 1.5v6h4v-6z"/></svg>(555)210-4187</li>
      <li><svg viewBox="0 0 10 10"><path d="M0 2h10v6H0zm1 1 4 3 4-3z" fill-rule="evenodd"/></svg>sales@veldmarksupplies.com</li>
      <li><svg viewBox="0 0 10 10"><circle cx="5" cy="5" r="5"/></svg>www.veldmarksupplies.com</li>
    </ul>
  </div>
  <svg class="card-bands" viewBox="0 0 540 14" preserveAspectRatio="none" aria-hidden="true">
    <polygon points="0,4 345,4 340,14 0,14" fill="var(--red)"/>
    <polygon points="355,4 540,4 540,14 350,14" fill="var(--blue)"/>
  </svg>
</section>

</body>
</html>
```